Business Card Design - Amberfield Court

We are looking at a new design for our business cards that has a modern and professional look. We run a residential aged care facility focussing on the care of residents. The cards will be used for potential clients, consultants and business opportunities in this sector. Blue and white is our main colours and would to see these colours incorporated in the design.
Industry/Entity Type
Business
Contact Information for Business Card
Amberfield Court, Darren Walsh, dwalsh@amberfieldcourt.com.au, Finance Manager, 0472 639 208, BCom, 37 Marrabel Crescent, Brindle Vale, Qld 4093.
Look and feel
Each slider illustrates characteristics of the customer's brand and the style your logo design should communicate.

```html
<!DOCTYPE html>
<html lang="en">
<head>
<meta charset="utf-8">
<title>Amberfield Court — Business Card</title>
<link href="https://fonts.googleapis.com/css2?family=Source+Sans+3:ital,wght@0,400;0,600;1,400&display=swap" rel="stylesheet">
<style>
  :root {
    --stage: #000000;
    --card: #dde5ea;
    --brand-blue: #4f7b94;
    --ink: #1e2328;
    --rule: #a9b6bf;
    --tagline-band: #b2a79f;
    --tagline-text: #ffffff;
  }
  * { margin: 0; padding: 0; box-sizing: border-box; }
  html, body {
    width: 1200px; height: 900px; overflow: hidden;
    background: var(--stage);
    font-family: "Source Sans 3", "Myriad Pro", Arial, sans-serif;
  }
  .canvas { position: relative; width: 1200px; height: 900px; }
  .card {
    position: absolute; top: 271px;
    width: 457px; height: 281px;
    background: var(--card);
    border-radius: 14px;
  }
  .card--front { left: 137px; }
  .card--back { left: 626px; }

  /* front */
  .front-brand {
    position: absolute; left: 36px; top: 128px; width: 180px;
    display: flex; align-items: center; justify-content: center; gap: 8px;
    color: var(--brand-blue); font-size: 19px; font-weight: 600;
    white-space: nowrap;
  }
  .brand-dot {
    width: 12px; height: 12px; border-radius: 50%;
    background: var(--brand-blue); flex: none;
  }
  .divider {
    position: absolute; left: 217px; top: 72px;
    width: 1px; height: 142px; background: var(--rule);
  }
  .contact { position: absolute; left: 235px; top: 70px; color: var(--ink); }
  .contact__name {
    color: var(--brand-blue); font-size: 18px; font-weight: 600; line-height: 1;
  }
  .contact__credential { font-size: 12px; font-weight: 600; }
  .contact__role { font-size: 13.5px; margin-top: 4px; }
  .contact__address { font-size: 13.5px; line-height: 19px; margin-top: 15px; }
  .contact__lines { margin-top: 14px; font-size: 13.5px; line-height: 20px; }
  .contact__line { display: flex; align-items: center; gap: 5px; }
  .contact__line svg { width: 10px; height: 10px; fill: var(--brand-blue); flex: none; }

  /* back */
  .back-brand {
    position: absolute; left: 0; right: 0; top: 150px;
    display: flex; align-items: center; justify-content: center; gap: 12px;
    color: var(--brand-blue); font-size: 30px; font-weight: 600;
    letter-spacing: 0.5px;
  }
  .back-brand .brand-dot { width: 18px; height: 18px; }
  .tagline {
    position: absolute; left: 111px; top: 209px;
    width: 236px; height: 22px;
    background: var(--tagline-band); color: var(--tagline-text);
    font-size: 16.5px; font-style: italic; line-height: 22px;
    text-align: center; white-space: nowrap;
  }
</style>
</head>
<body>
<div class="canvas">
  <section class="card card--front" aria-label="Business card front">
    <div class="front-brand"><span class="brand-dot"></span>Amberfield Court</div>
    <div class="divider"></div>
    <div class="contact">
      <p class="contact__name">Darren Walsh, <span class="contact__credential">BCom</span></p>
      <p class="contact__role">Finance Manager</p>
      <p class="contact__address">37 Marrabel Crescent,<br>Brindle Vale, Qld 4093</p>
      <div class="contact__lines">
        <p class="contact__line">
          <svg viewBox="0 0 24 24" aria-hidden="true"><path d="M6.6 10.8a15.1 15.1 0 0 0 6.6 6.6l2.2-2.2c.3-.3.7-.4 1-.2 1.1.4 2.3.6 3.6.6.6 0 1 .4 1 1V20c0 .6-.4 1-1 1A17 17 0 0 1 3 4c0-.6.4-1 1-1h3.5c.6 0 1 .4 1 1 0 1.3.2 2.5.6 3.6.1.3 0 .7-.2 1z"/></svg>
          0472 639 208
        </p>
        <p class="contact__line">
          <svg viewBox="0 0 24 24" aria-hidden="true"><path d="M2 5h20v14H2z"/><path d="M3 6l9 6.3L21 6" stroke="var(--card)" stroke-width="1.6" fill="none"/></svg>
          dwalsh@amberfieldcourt.com.au
        </p>
      </div>
    </div>
  </section>

  <section class="card card--back" aria-label="Business card back">
    <div class="back-brand"><span class="brand-dot"></span>Amberfield Court</div>
    <p class="tagline">Comfort, Respect, Belonging</p>
  </section>
</div>
</body>
</html>
```